One piece Trade show banner, 8' x 8' square

One piece banner for trade show
8' x 8' airborne geophysical company

Target Market(s)

Business

Industry/Entity Type

mineral exploration and science

Colors
0054AA
0677BA
7BADD7
CADEEF
E8F1F8
FFC000
F8CF3A
FAE287
FDF2CF
FEFAEE

Requirements
Must have
• Company logo (attached), slogan (Airborne Geophysics for Discovery). We are looking for a new banner, for a standard 8 x 8' square one-piece booth. I have attached some pictures, our logo, our old banner for reference, and two examples from unrelated companies from a tradeshow that we like. If its possible I'd like to change the color of the helicopter from green to dark grey. IE, keep the orange and white, just change green to dark grey. Looking for a simple, clean design with minimal text.
Nice to have
• I have attached examples of banners that we like (2xIMG), plus our old 3-piece banner r.
Should not have
• Green in the helicopter. Please change the color of the helicopter with green/orange/white to dark grey/orange/white. IE change the green to dark grey and leave the orange and white alone. I've attached lots of pictures but I don't expect them all to be used.

```html
<!DOCTYPE html>
<html lang="en">
<head>
<meta charset="utf-8">
<title>Vantage AeroSurveys – Airborne Geophysics for Discovery</title>
<link rel="stylesheet" href="https://fonts.googleapis.com/css2?family=Roboto+Condensed:ital,wght@0,400;0,700;0,800;1,700;1,800&family=Jost:wght@400&display=swap">
<style>
  :root {
    --sky-top: #e4f0fa;
    --sky-mid: #6fb4ea;
    --sky-low: #4f9fe4;
    --sky-bottom: #aad3f3;
    --cyan-panel: #5bcbe9;
    --gold-panel: #e3ae48;
    --ink: #050505;
    --craft-light: #7f9cc4;
    --craft-dark: #3a5780;
  }
  * { margin: 0; padding: 0; box-sizing: border-box; }
  html, body { width: 1200px; height: 1200px; overflow: hidden; }
  body { font-family: "Roboto Condensed", Arial, sans-serif; color: var(--ink); }

  .banner { position: relative; width: 1200px; height: 1200px; overflow: hidden; }

  .sky {
    position: absolute; inset: 0;
    background:
      radial-gradient(ellipse 70% 30% at 25% 22%, rgba(255,255,255,.75), transparent 70%),
      radial-gradient(ellipse 50% 25% at 85% 40%, rgba(255,255,255,.55), transparent 70%),
      linear-gradient(180deg, var(--sky-top) 0%, var(--sky-mid) 40%, var(--sky-low) 55%, var(--sky-bottom) 100%);
  }

  .brand { position: absolute; left: 65px; top: 36px; color: var(--ink); font-family: "Jost", Arial, sans-serif; font-weight: 400; line-height: 1; }
  .brand-name { display: block; font-size: 56px; letter-spacing: 0.5px; }
  .brand-sub { display: block; font-size: 18px; margin-top: 2px; text-align: right; }

  .panel { position: absolute; }
  .panel-cyan {
    left: 330px; top: 106px; width: 468px; height: 868px;
    background: var(--cyan-panel);
    border-radius: 0 236px 0 242px;
  }
  .panel-gold {
    left: 576px; top: 268px; width: 486px; height: 868px;
    background: var(--gold-panel);
    border-radius: 0 250px 0 250px;
  }

  .services { position: absolute; left: 373px; top: 168px; list-style: none; }
  .services li { font-size: 32px; font-weight: 400; line-height: 58px; letter-spacing: 0.2px; }

  .slogan {
    position: absolute; left: 598px; top: 340px;
    font-weight: 800; font-size: 80px; line-height: 103px; letter-spacing: -0.5px;
  }
  .slogan em { font-style: italic; font-weight: 700; }

  .aircraft {
    position: absolute; left: 0; top: 650px; width: 1060px; height: 390px;
    border-radius: 200px 60px 120px 60px;
    background: linear-gradient(160deg, var(--craft-light) 0%, var(--craft-dark) 100%);
  }
</style>
</head>
<body>
  <main class="banner">
    <div class="sky" role="img" aria-label="Bright blue sky with soft white clouds"></div>

    <div class="brand">
      <span class="brand-name">Vantage</span>
      <span class="brand-sub">AeroSurveys</span>
    </div>

    <div class="panel panel-cyan"></div>
    <div class="panel panel-gold"></div>

    <ul class="services">
      <li>ELECTROMAGNETICS</li>
      <li>RADIOMETRICS</li>
      <li>MAGNETICS</li>
    </ul>

    <h1 class="slogan">AIRBORNE<br>GEOPHYSICS<br><em>FOR</em> Discovery</h1>

    <div class="aircraft" role="img" aria-label="Photo of a dark grey survey helicopter with orange and white stripes in flight"></div>
  </main>
</body>
</html>
```